New Bicycle shop business card

Hi!
I'm looking for a business card for my new proffesional bike mechanics shop. This shop is only for fixing broken bikes and not selling bikes.
Peferbly a modern and sleek and modern design.
Colors: black, grey, red, white
Information:
Name: Rijwielwerkplaats Vanhoutte
Shop owner: Bart Vanhoutte & Marieke Segers
Website: www.rijwielwerkplaats-vanhoutte.be
Email: info@rijwielwerkplaats-vanhoutte.be
Phone number: +32471902368
Street adres: Kerkweg 46
9940 Bellebeke
Slogan/shop information: Herstellingen van alle merken.
Logo: see files.
Target Market(s)
People who seek a mechanic to fix or upgrade their bikes.
Contact Information for Business Card
Information:
Website: info@rijwielwerkplaats-vanhoutte.be
9940 Bellebeke
Logo: see files.

```html
<!DOCTYPE html>
<html lang="nl">
<head>
<meta charset="utf-8">
<title>Rijwielwerkplaats Vanhoutte – visitekaartje</title>
<link rel="stylesheet" href="https://fonts.googleapis.com/css2?family=Lato:wght@400;700;900&display=swap">
<style>
  :root {
    --backdrop: #2b2b2b;
    --paper: #ffffff;
    --brand-red: #dc2330;
    --ink: #1c1616;
    --text-grey: #3d3d3d;
    --rule-grey: #b5b5b5;
  }
  * { margin: 0; padding: 0; box-sizing: border-box; }
  html, body { width: 1200px; height: 1200px; overflow: hidden; }
  body {
    background: var(--backdrop);
    font-family: "Lato", sans-serif;
    position: relative;
  }
  .card {
    position: absolute;
    top: 310px;
    height: 594px;
    text-align: center;
  }
  .card--front { left: 234px; width: 364px; background: var(--paper); }
  .card--back  { left: 627px; width: 369px; background: var(--brand-red); }

  .brand-dot {
    position: absolute;
    left: 50%;
    top: 92px;
    width: 56px;
    height: 56px;
    margin-left: -28px;
    border-radius: 50%;
    background: var(--brand-red);
  }
  .brand-name {
    font-weight: 900;
    text-transform: uppercase;
    line-height: 1.15;
  }
  .card--front .brand-name {
    position: absolute;
    top: 188px;
    left: 0; right: 0;
    color: var(--ink);
    font-size: 25px;
    letter-spacing: 1px;
  }
  .brand-name .second-line { letter-spacing: 9px; display: block; }

  .owners {
    position: absolute;
    top: 340px;
    left: 0; right: 0;
    color: var(--brand-red);
    font-size: 16px;
    font-weight: 700;
    text-transform: uppercase;
  }
  .role {
    position: absolute;
    top: 360px;
    left: 0; right: 0;
    color: var(--text-grey);
    font-size: 17px;
  }
  .icon-row {
    position: absolute;
    top: 395px;
    left: 87px;
    width: 190px;
    height: 26px;
  }
  .contact-lines, .address-lines {
    position: absolute;
    left: 0; right: 0;
    color: var(--text-grey);
    font-size: 16.5px;
    line-height: 21.5px;
  }
  .contact-lines { top: 431px; }
  .address-lines { top: 518px; }
  .divider {
    position: absolute;
    top: 507px;
    left: 88px;
    width: 195px;
    height: 1px;
    background: #d6d6d6;
  }

  .card--back .brand-name {
    position: absolute;
    top: 257px;
    left: 0; right: 0;
    color: var(--paper);
    font-size: 27px;
    letter-spacing: 1.5px;
  }
  .tagline {
    position: absolute;
    top: 347px;
    left: 0; right: 0;
    color: var(--paper);
    font-size: 17px;
    text-transform: uppercase;
  }
</style>
</head>
<body>
  <section class="card card--front">
    <div class="brand-dot"></div>
    <h1 class="brand-name">Rijwielwerkplaats<span class="second-line">Vanhoutte</span></h1>
    <p class="owners">Bart Vanhoutte &amp; Marieke Segers</p>
    <p class="role">Owner</p>
    <svg class="icon-row" viewBox="0 0 190 26" aria-hidden="true">
      <line x1="0" y1="13" x2="52" y2="13" stroke="#b5b5b5" stroke-width="1.5"/>
      <line x1="138" y1="13" x2="190" y2="13" stroke="#b5b5b5" stroke-width="1.5"/>
      <circle cx="67" cy="13" r="12" fill="#dc2330"/>
      <circle cx="95" cy="13" r="12" fill="#dc2330"/>
      <circle cx="123" cy="13" r="12" fill="#dc2330"/>
      <path d="M61 9 q6-4 12 0 v2 h-3 v-1 h-6 v1 h-3z M62 13 h10 v5 h-10z" fill="#fff"/>
      <rect x="89" y="9" width="12" height="8" fill="none" stroke="#fff" stroke-width="1.5"/>
      <path d="M89 9 l6 5 l6 -5" fill="none" stroke="#fff" stroke-width="1.5"/>
      <circle cx="123" cy="13" r="6" fill="none" stroke="#fff" stroke-width="1.5"/>
      <path d="M117 13 h12 M123 7 q-4 6 0 12 q4 -6 0 -12" fill="none" stroke="#fff" stroke-width="1.2"/>
    </svg>
    <p class="contact-lines">+32471902368<br>info@rijwielwerkplaats-vanhoutte.be<br>www.rijwielwerkplaats-vanhoutte.be</p>
    <div class="divider"></div>
    <p class="address-lines">Kerkweg 46<br>9940 Bellebeke</p>
  </section>

  <section class="card card--back">
    <h2 class="brand-name">Rijwielwerkplaats<span class="second-line">Vanhoutte</span></h2>
    <p class="tagline">Herstellingen van alle merken</p>
  </section>
</body>
</html>
```